Website design for luxury private hair salon

I'm looking for someone to use my Logo and build me a website for my webpage www.corsetresses.com.au (You can have a look at it as it has every detail I need included on it already), however I want a fresh new appearance and it to look and feel super stylish.

I am thinking colours in black, with silver or white, beautiful hair images like the ones you'll see on the current webpage - the price list as per what you already see.

I will include a copy of my biz card on here, so you can see the feel of the card, and design a website with a similar feel. It is matt black with a foil silver.

Modern, but classic and fresh. I will also need you to be able to publish it to my URL for me as I have no idea how to do this. I need it up and running pronto!

The website will need to be able to be read clearly on all devices incluing smart phones and ipads. The URL is currently registered and hosted by Norvel Web

Thinking a Home Page - large logo etc and write up on who and what we offer
Services/Price List page - as per the price list on my current webpage
Contact Page - with a built in contact form.

Target Market(s)

Middle aged, fashionable, stylish women and men who enjoy luxury hair care and styling in an upmarket location.

Industry/Entity Type

Hair And Beauty

Number of Pages Required

3 page

Font styles to use
Other font styles liked:
• see my images for my current logo

Colors
000000
b2b2b2
a54499

Requirements
Must have
• Style
• Fast turnaround
• Be viewable on all devices, PC, ipads, smart phones
• Designer able to upload it so its a running website for me to my URL
Nice to have
• Just a really feminine, stylish website which is easy to read and shows some beautiful images of perfect hair
Should not have
• Browns, reds or orange colours.

```html
<!DOCTYPE html>
<html lang="en">
<head>
<meta charset="utf-8">
<title>Corsetresses – Private Luxury Hair Salon</title>
<link rel="stylesheet" href="https://fonts.googleapis.com/css2?family=Open+Sans:wght@300;400;600;700&display=swap">
<style>
  :root {
    --purple: #a54499;
    --purple-dark: #8f3a85;
    --ink: #333333;
    --body-text: #666666;
    --muted: #9a9a9a;
    --line: #e3e3e3;
    --panel: #f9f9f9;
    --white: #ffffff;
  }
  * { box-sizing: border-box; margin: 0; padding: 0; }
  html, body { width: 1200px; height: 2736px; overflow: hidden; }
  body { position: relative; font-family: "Open Sans", Arial, sans-serif; color: var(--ink); background: var(--white); }

  /* Hero */
  .hero { position: absolute; left: 0; top: 0; width: 1200px; height: 671px; overflow: hidden; }
  .hero-photo { position: absolute; inset: 0;
    background: radial-gradient(ellipse at 78% 35%, #b69a84 0%, #7d6a5e 35%, #4f4a49 70%, #3d3b3c 100%); }
  .hero-shade { position: absolute; inset: 0; background: rgba(40,40,44,0.25); }
  .nav { position: absolute; top: 62px; left: 0; width: 1200px; height: 24px; }
  .nav a { position: absolute; top: 0; font-size: 14px; font-weight: 600; color: var(--white); text-decoration: none; letter-spacing: 0.2px; transform: translateX(-50%); white-space: nowrap; }
  .nav a.is-active { color: var(--purple); }
  .brand { position: absolute; top: 52px; left: 600px; transform: translateX(-50%); text-align: center; color: var(--white); font-size: 26px; font-weight: 300; letter-spacing: 0.5px; white-space: nowrap; }
  .hero-title { position: absolute; top: 362px; left: 0; width: 1200px; text-align: center; font-size: 37px; font-weight: 300; color: var(--white); }
  .btn { display: block; position: absolute; background: var(--purple); color: var(--white); text-align: center; text-decoration: none; font-weight: 700; text-transform: uppercase; }
  .btn-hero { left: 441px; top: 458px; width: 318px; height: 54px; line-height: 54px; font-size: 20px; letter-spacing: 0.3px; }
  .dots { position: absolute; top: 590px; left: 572px; display: flex; gap: 12px; }
  .dots span { width: 6px; height: 6px; border-radius: 50%; background: var(--white); }
  .dots span.is-current { background: var(--purple); }

  /* Who we are */
  .video-frame { position: absolute; left: 144px; top: 764px; width: 429px; height: 267px; background: #f1f1f1; border: 1px solid #dcdcdc; box-shadow: 0 3px 6px rgba(0,0,0,0.15); padding: 8px; }
  .video-still { width: 100%; height: 100%; background: linear-gradient(180deg, #c98a3a 0%, #8c7b4a 40%, #4d5a35 70%, #2d3326 100%); position: relative; }
  .play { position: absolute; left: 50%; top: 50%; transform: translate(-50%,-50%); }
  .section-title { position: absolute; font-size: 40px; font-weight: 400; color: var(--purple); }
  .who-title { left: 600px; top: 752px; }
  .who-text { position: absolute; left: 604px; top: 838px; width: 460px; font-size: 13.5px; line-height: 28px; color: var(--body-text); }
  .btn-small { left: 600px; top: 994px; width: 110px; height: 33px; line-height: 33px; font-size: 12px; font-weight: 600; }

  /* Offer */
  .offer { position: absolute; left: 0; top: 1120px; width: 1200px; height: 689px; background: var(--panel); }
  .center-title { left: 0; width: 1200px; text-align: center; }
  .service { position: absolute; width: 215px; }
  .service-head { display: flex; align-items: center; gap: 14px; height: 44px; }
  .service-head svg { flex: 0 0 auto; }
  .service-name { font-size: 14px; font-weight: 600; color: var(--ink); }
  .service-text { margin-top: 12px; font-size: 12px; line-height: 19px; color: var(--muted); }

  /* Contact */
  .field { position: absolute; border: 1px solid var(--line); background: var(--white); font-size: 11px; color: #b0b0b0; padding: 0 20px; line-height: 50px; white-space: nowrap; overflow: hidden; }
  .field-area { line-height: 1; padding-top: 20px; }
  .btn-send { left: 531px; top: 2231px; width: 137px; height: 40px; line-height: 40px; font-size: 13px; font-weight: 600; }
  .partner { position: absolute; top: 2327px; height: 92px; }
  .partner-a { left: 197px; width: 389px; background: linear-gradient(90deg, #6b5336 0%, #2a2420 45%, #121212 100%); }
  .partner-b { left: 613px; width: 390px; background: linear-gradient(90deg, #f4f4f4 0%, #d9d2e6 40%, #c7a7c9 70%, #e9e9e9 100%); border: 1px solid var(--line); }

  /* Footer */
  .footer { position: absolute; left: 0; top: 2490px; width: 1200px; height: 246px; background: var(--panel); }
  .footer-brand { position: absolute; top: 72px; left: 0; width: 1200px; text-align: center; font-size: 30px; font-weight: 300; color: var(--ink); letter-spacing: 0.5px; }
  .footer-nav { position: absolute; top: 165px; left: 0; width: 1200px; text-align: center; font-size: 12px; color: var(--ink); }
  .footer-nav a { color: inherit; text-decoration: none; }
  .footer-nav .sep { margin: 0 18px; }
  .copyright { position: absolute; top: 198px; left: 0; width: 1200px; text-align: center; font-size: 11px; color: var(--ink); }
</style>
</head>
<body>

<header class="hero">
  <div class="hero-photo" role="img" aria-label="Close-up photograph of a woman with long flowing glossy hair over her shoulder"></div>
  <div class="hero-shade"></div>
  <nav class="nav">
    <a class="is-active" style="left:177px">HOME</a>
    <a style="left:277px">ABOUT US</a>
    <a style="left:399px">WHO WE ARE</a>
    <a style="left:755px">WHAT WE OFFER</a>
    <a style="left:889px">PRICE LIST</a>
    <a style="left:1012px">CONTACT US</a>
  </nav>
  <div class="brand">Corsetresses</div>
  <h1 class="hero-title">We are a private luxury hair salon in Australia</h1>
  <a class="btn btn-hero">Make an appointment</a>
  <div class="dots"><span class="is-current"></span><span></span><span></span><span></span></div>
</header>

<section class="who">
  <div class="video-frame">
    <div class="video-still" role="img" aria-label="Video still of a woman with long hair in a sunlit field at sunset">
      <svg class="play" width="80" height="80" viewBox="0 0 80 80"><circle cx="40" cy="40" r="36" fill="none" stroke="#fff" stroke-width="4"/><path d="M31 24 L57 40 L31 56 Z" fill="#fff"/></svg>
    </div>
  </div>
  <h2 class="section-title who-title">Who We Are ?</h2>
  <p class="who-text">We pride ourselves on being able to offer a private salon experience to our clients in the exclusive suburb of Bellmere, where your hair design and colouring needs will be met with years of experience and current industry training and knowledge</p>
  <a class="btn btn-small">LEARN MORE</a>
</section>

<section class="offer">
  <h2 class="section-title center-title" style="top:82px">What We Offer</h2>

  <div class="service" style="left:144px; top:210px">
    <div class="service-head"><svg width="40" height="42" viewBox="0 0 40 42" fill="none" stroke="#a54499" stroke-width="4"><circle cx="9" cy="33" r="6"/><circle cx="31" cy="33" r="6"/><path d="M13 28 L33 2 M27 28 L7 2"/></svg><span class="service-name">Hair Cuts</span></div>
    <p class="service-text">Sed ut perspiciatis unde omnis iste natus error sit voluptatem accusantium doloremque laudantium, totam rem aperiam, eaque ipsa quae</p>
  </div>
  <div class="service" style="left:378px; top:210px">
    <div class="service-head"><svg width="28" height="40" viewBox="0 0 28 40"><rect x="2" y="2" width="24" height="36" fill="none" stroke="#a54499" stroke-width="3"/><g fill="#a54499"><rect x="7" y="8" width="5" height="5"/><rect x="16" y="8" width="5" height="5"/><rect x="7" y="17" width="5" height="5"/><rect x="16" y="17" width="5" height="5"/><rect x="7" y="26" width="5" height="5"/><rect x="16" y="26" width="5" height="5"/></g></svg><span class="service-name">Colouring</span></div>
    <p class="service-text">Sed ut perspiciatis unde omnis iste natus error sit voluptatem accusantium doloremque laudantium, totam rem aperiam, eaque ipsa quae</p>
  </div>
  <div class="service" style="left:611px; top:210px">
    <div class="service-head"><svg width="28" height="44" viewBox="0 0 28 44" fill="#a54499"><rect x="2" y="2" width="6" height="40" rx="2"/><rect x="15" y="14" width="10" height="28" rx="2"/><path d="M17 14 L20 4 L23 14 Z"/></svg><span class="service-name">Highlighting</span></div>
    <p class="service-text">Sed ut perspiciatis unde omnis iste natus error sit voluptatem accusantium doloremque laudantium, totam rem aperiam, eaque ipsa quae</p>
  </div>
  <div class="service" style="left:845px; top:210px">
    <div class="service-head"><svg width="30" height="42" viewBox="0 0 30 42" fill="none" stroke="#a54499" stroke-width="5"><path d="M4 40 V16 A11 11 0 0 1 26 16 V40"/></svg><span class="service-name">Extensions</span></div>
    <p class="service-text">Sed ut perspiciatis unde omnis iste natus error sit voluptatem accusantium doloremque laudantium, totam rem aperiam, eaque ipsa quae</p>
  </div>

  <div class="service" style="left:144px; top:427px">
    <div class="service-head"><svg width="28" height="48" viewBox="0 0 28 48" fill="none" stroke="#a54499" stroke-width="4"><path d="M4 2 L12 40 M24 2 L16 40 M12 40 L14 46 L16 40"/></svg><span class="service-name">Straightening</span></div>
    <p class="service-text">Sed ut perspiciatis unde omnis iste natus error sit voluptatem accusantium doloremque laudantium, totam rem aperiam, eaque ipsa quae</p>
  </div>
  <div class="service" style="left:378px; top:427px">
    <div class="service-head"><svg width="34" height="48" viewBox="0 0 34 48" fill="#a54499"><path d="M11 2 H23 L21 16 L32 46 H2 L13 16 Z"/></svg><span class="service-name">Bridal</span></div>
    <p class="service-text">Sed ut perspiciatis unde omnis iste natus error sit voluptatem accusantium doloremque laudantium, totam rem aperiam, eaque ipsa quae</p>
  </div>
  <div class="service" style="left:611px; top:427px">
    <div class="service-head"><svg width="34" height="42" viewBox="0 0 34 42" fill="#a54499"><rect x="12" y="2" width="8" height="8"/><path d="M8 12 H24 L30 22 V40 H2 V22 Z"/></svg><span class="service-name">Treatments</span></div>
    <p class="service-text">Sed ut perspiciatis unde omnis iste natus error sit voluptatem accusantium doloremque laudantium, totam rem aperiam, eaque ipsa quae</p>
  </div>
  <div class="service" style="left:845px; top:427px">
    <div class="service-head"><svg width="32" height="42" viewBox="0 0 32 42" fill="none" stroke="#a54499" stroke-width="3"><rect x="2" y="2" width="28" height="38"/><path d="M16 2 V40 M2 14 H16 M16 28 H30"/></svg><span class="service-name">Products &amp; Advice</span></div>
    <p class="service-text">Sed ut perspiciatis unde omnis iste natus error sit voluptatem accusantium doloremque laudantium, totam rem aperiam, eaque ipsa quae</p>
  </div>
</section>

<section class="contact">
  <h2 class="section-title center-title" style="top:1862px">Contact Us</h2>
  <div class="field" style="left:223px; top:1965px; width:364px; height:52px">May we know your name?</div>
  <div class="field" style="left:223px; top:2049px; width:364px; height:52px">What is your email address?</div>
  <div class="field" style="left:223px; top:2134px; width:364px; height:52px">Or if you'd prefer we call you, let us know your number here...</div>
  <div class="field field-area" style="left:611px; top:1965px; width:367px; height:220px">What can we help you with?</div>
  <a class="btn btn-send">SEND</a>
  <div class="partner partner-a" role="img" aria-label="Partner banner for Lumen Haircare with a model's flowing hair"></div>
  <div class="partner partner-b" role="img" aria-label="Partner banner for Verity Pro showing a row of haircare product bottles"></div>
</section>

<footer class="footer">
  <div class="footer-brand">Corsetresses</div>
  <nav class="footer-nav">
    <a>HOME</a><span class="sep">|</span><a>ABOUT US</a><span class="sep">|</span><a>WHO WE ARE</a><span class="sep">|</span><a>WHAT WE OFFER</a><span class="sep">|</span><a>PRICE LIST</a><span class="sep">|</span><a>CONTACT US</a>
  </nav>
  <p class="copyright">© 2017 COMPANY NAME &nbsp;|&nbsp; ALL RIGHTS RESERVED</p>
</footer>

</body>
</html>
```